Clinic for cellulit and fat removal

Name of clinic :
Lirava
- Body & Health (this has to be written on the site.)
I need CMS for me to be able to make changes myself.
A webpage for woman searching for a solution to remove fat and cellulit.
The owner is a brazilian woman in Denmark, and want her sense of aestetic shines thru the website.
There needs to be a slide show on the landing page showing big sliding pictures, of the clinic and and the treatments.
The Cryolipolysis, is a treatment freezing fat and cellulit, and this treatment will be the Attraction of the clinic.
Needs These pages in a horisontal fasion. (written in Danish)
Lirava
Behandlinger
- Cryolipolysis
- Trimflox
- Lymfemassage
- Korathelix
- Amberline Tide
Produkter
Priser
Kontakt
Clinic
Coded - Design and coding required
5+ page

```html
<!DOCTYPE html>
<html lang="da">
<head>
<meta charset="utf-8">
<title>Lirava – Body &amp; Health</title>
<link href="https://fonts.googleapis.com/css2?family=Mulish:wght@300;400;600&display=swap" rel="stylesheet">
<style>
:root{
  --ink:#111;
  --text:#555;
  --muted:#8a8a8a;
  --line:#e6e6e6;
  --white:#fff;
  --hero-a:#c9977a;
  --hero-b:#a8694a;
  --hero-c:#e4c4b0;
  --banner-a:#5d5957;
  --banner-b:#b59a8c;
}
*{margin:0;padding:0;box-sizing:border-box}
html,body{width:1200px;height:4255px;overflow:hidden;background:var(--white)}
body{font-family:"Mulish",Arial,sans-serif;color:var(--ink);position:relative}
a{color:inherit;text-decoration:none}

.site-header{position:absolute;left:0;top:0;width:1200px;height:113px}
.brand{position:absolute;left:94px;top:30px;font-weight:300;font-size:44px;letter-spacing:1px}
.main-nav{position:absolute;left:443px;top:44px;display:flex;gap:38px;font-size:17px}
.main-nav a.active{border-bottom:2px solid var(--ink);padding-bottom:10px}
.lang{position:absolute;left:976px;top:42px;display:flex;align-items:center;gap:14px;font-size:13px}
.lang .on{background:var(--ink);color:var(--white);border-radius:14px;padding:5px 18px}

.hero{position:absolute;left:0;top:113px;width:1200px;height:653px;
  background:linear-gradient(120deg,var(--hero-c) 0%,var(--hero-a) 45%,var(--hero-b) 100%)}
.hero-copy{position:absolute;left:0;top:300px;width:1200px;text-align:center;color:var(--white)}
.hero-title{font-weight:400;font-size:56px;line-height:1}
.hero-sub{font-size:17px;margin-top:14px}
.btn-outline{display:inline-block;border:1.5px solid var(--white);color:var(--white);border-radius:30px;
  font-size:14px;letter-spacing:.5px;padding:16px 40px}
.hero .btn-outline{margin-top:38px;width:243px}
.dots{position:absolute;left:0;top:576px;width:1200px;display:flex;justify-content:center;gap:12px}
.dots span{width:8px;height:8px;border-radius:50%;background:rgba(255,255,255,.7)}
.dots span:first-child{background:var(--white)}

.section-title{position:absolute;left:0;top:825px;width:1200px;text-align:center;font-size:36px;font-weight:400}

.treatment{position:absolute;left:108px;width:981px;height:311px}
.treatment .photo{position:absolute;top:0;width:479px;height:311px}
.treatment .copy{position:absolute;width:480px}
.treatment.img-right .photo{left:502px}
.treatment.img-right .copy{left:0;top:22px}
.treatment.img-left .photo{left:0}
.treatment.img-left .copy{left:502px;top:10px}
.treatment h3{font-size:24px;font-weight:400;margin-bottom:22px}
.treatment p{font-size:12.5px;line-height:28px;color:var(--muted)}
.btn-dark{display:inline-block;background:var(--ink);color:var(--white);border-radius:22px;font-size:12.5px;
  padding:13px 32px;margin-top:38px}

.ph-cryo{background:linear-gradient(135deg,#e9e4e2,#c7bcc0 60%,#8c7aa0)}
.ph-trim{background:linear-gradient(135deg,#2c2a2b,#4d3d35 55%,#1a1a1a)}
.ph-lymf{background:linear-gradient(135deg,#f3ece6,#d6b8a3 60%,#c4a08a)}
.ph-kora{background:linear-gradient(120deg,#c3d6df,#e8eef2 55%,#9fb6c4)}
.ph-amber{background:radial-gradient(circle at 62% 42%,#c9b680 0,#3a3530 22%,#0c0c0c 60%)}

.feature{position:absolute;left:0;top:3197px;width:1200px;height:656px;
  background:linear-gradient(100deg,var(--banner-a) 0%,var(--banner-b) 55%,#d8cfc9 100%)}
.feature-text{position:absolute;left:235px;top:250px;width:640px;color:var(--white);font-size:31px;line-height:39px;font-weight:400}
.feature .btn-outline{position:absolute;left:241px;top:409px;width:244px;text-align:center;padding:15px 0}

.site-footer{position:absolute;left:0;top:3900px;width:1200px}
.foot-col{position:absolute;top:20px}
.foot-col h4{font-size:13px;font-weight:600;margin-bottom:28px}
.foot-col li{list-style:none;font-size:12.5px;line-height:28px;color:#333}
.social{display:flex;gap:11px}
.social span{width:30px;height:30px;border-radius:50%;background:#c7c7c7}
.social span:first-child{background:var(--ink)}
.bottom-bar{position:absolute;left:0;top:4160px;width:1200px;height:95px;border-top:1px solid var(--line)}
.bottom-brand{position:absolute;left:94px;top:22px;font-size:32px;font-weight:300}
.copyright{position:absolute;left:828px;top:40px;font-size:12px;color:#333}
.copyright span{margin-left:44px}
</style>
</head>
<body>

<header class="site-header">
  <a class="brand" href="#">Lirava</a>
  <nav class="main-nav">
    <a class="active" href="#">Lirava</a>
    <a href="#">Behandlinger</a>
    <a href="#">Produkter</a>
    <a href="#">Priser</a>
    <a href="#">Kontakt</a>
  </nav>
  <div class="lang"><span class="on">English</span><span>Danish</span></div>
</header>

<section class="hero" role="img" aria-label="Slideshow photo of a body treatment in the clinic">
  <div class="hero-copy">
    <h1 class="hero-title">Body &amp; Health</h1>
    <p class="hero-sub">We are a cellulit and fat removal clinic</p>
    <a class="btn-outline" href="#">BOOK AN APPOINTMENT</a>
  </div>
  <div class="dots"><span></span><span></span><span></span><span></span></div>
</section>

<h2 class="section-title">Our Treatments</h2>

<article class="treatment img-right" style="top:970px">
  <div class="copy">
    <h3>Cryolipolysis</h3>
    <p>Our gentle treatment is planned around your body and goals, with calm guidance at every step. Sessions are short, safe and relaxing, and most clients return to daily life right away with visible and lasting results. Every plan begins with a personal consultation where we listen, measure and explain the options. We use modern equipment in a warm, quiet room, so you can feel at ease while the work is done.</p>
    <a class="btn-dark" href="#">Read More</a>
  </div>
  <div class="photo ph-cryo" role="img" aria-label="Photo of a woman receiving a cryolipolysis treatment"></div>
</article>

<article class="treatment img-left" style="top:1405px">
  <div class="photo ph-trim" role="img" aria-label="Photo of a woman training with dumbbells"></div>
  <div class="copy">
    <h3>Trimflox</h3>
    <p>Our gentle treatment is planned around your body and goals, with calm guidance at every step. Sessions are short, safe and relaxing, and most clients return to daily life right away with visible and lasting results. Every plan begins with a personal consultation where we listen, measure and explain the options. We use modern equipment in a warm, quiet room, so you can feel at ease while the work is done.</p>
    <a class="btn-dark" href="#">Read More</a>
  </div>
</article>

<article class="treatment img-right" style="top:1840px">
  <div class="copy">
    <h3>Lymfemassage</h3>
    <p>Our gentle treatment is planned around your body and goals, with calm guidance at every step. Sessions are short, safe and relaxing, and most clients return to daily life right away with visible and lasting results. Every plan begins with a personal consultation where we listen, measure and explain the options. We use modern equipment in a warm, quiet room, so you can feel at ease while the work is done.</p>
    <a class="btn-dark" href="#">Read More</a>
  </div>
  <div class="photo ph-lymf" role="img" aria-label="Photo of a lymphatic back massage"></div>
</article>

<article class="treatment img-left" style="top:2273px">
  <div class="photo ph-kora" role="img" aria-label="Photo with a glowing light motif in cool tones"></div>
  <div class="copy">
    <h3>Korathelix</h3>
    <p>Our gentle treatment is planned around your body and goals, with calm guidance at every step. Sessions are short, safe and relaxing, and most clients return to daily life right away with visible and lasting results. Every plan begins with a personal consultation where we listen, measure and explain the options. We use modern equipment in a warm, quiet room, so you can feel at ease while the work is done.</p>
    <a class="btn-dark" href="#">Read More</a>
  </div>
</article>

<article class="treatment img-right" style="top:2711px">
  <div class="copy">
    <h3>Amberline Tide</h3>
    <p>Our gentle treatment is planned around your body and goals, with calm guidance at every step. Sessions are short, safe and relaxing, and most clients return to daily life right away with visible and lasting results. Every plan begins with a personal consultation where we listen, measure and explain the options. We use modern equipment in a warm, quiet room, so you can feel at ease while the work is done.</p>
    <a class="btn-dark" href="#">Read More</a>
  </div>
  <div class="photo ph-amber" role="img" aria-label="Photo of a hand holding a glowing light bulb on a dark background"></div>
</article>

<section class="feature" role="img" aria-label="Photo of a waist being measured with a tape measure">
  <p class="feature-text">The Cryolipolysis, is a treatment freezing fat and cellulit, and this treatment will be the Attraction of the clinic.</p>
  <a class="btn-outline" href="#">BOOK AN APPOINTMENT</a>
</section>

<footer class="site-footer">
  <div class="foot-col" style="left:94px">
    <h4>Menu Links</h4>
    <ul><li>Lirava</li><li>Produkter</li><li>Priser</li><li>Kontakt</li></ul>
  </div>
  <div class="foot-col" style="left:318px">
    <h4>Treatments</h4>
    <ul><li>Cryolipolysis</li><li>Trimflox</li><li>Lymfemassage</li><li>Korathelix</li><li>Amberline Tide</li></ul>
  </div>
  <div class="foot-col" style="left:547px">
    <h4>Contact Us</h4>
    <ul><li>Nordvind Studio</li><li>Vestergade 14</li><li>1456 København</li><li>+45 31 42 58 70</li><li>E-Mail: info@lirava.dk</li></ul>
  </div>
  <div class="foot-col" style="left:797px">
    <h4>Connect With Us</h4>
    <div class="social"><span></span><span></span><span></span><span></span><span></span><span></span></div>
  </div>
</footer>

<div class="bottom-bar">
  <span class="bottom-brand">Lirava</span>
  <p class="copyright">© 2017 Company Name | All Rights Reserved <span>CS</span></p>
</div>

</body>
</html>
```